Bright Harbor, LLC Business Card Design

We need a product business card designed for a new company Bright Harbor, LLC. We make and resell waterless RV cleaner, polish and protectant. It cleans and protects in a simple spray and wipe step leaving the surface protected and conditioned to repel dust, dirt, water, smudges, bugs and fingerprints while preventing fogging. Safe on acrylic, plexiglas, lexan, plastic, rubber, painted surfaces, chrome, stainless, aluminum, vinyl, leather, glass.... This is an eco-friendly green product.

We want to play off the company name to tell the consumer that the product is easy to use and associate to the nostalgics 1950's in the USA... Thinking old travel trailer with hot rod truck pulling it as the graphic, maybe the husband cleaning the truck and the wife cleaning the trailer for a Bright Harbor surface.
Updates

Just posted our newly finished logo. Need to have "Cleaner and Protectant" added to the design as well. Thanks everyone that has submitted thus far, i am working to get comments on all.

If you need a different file format, please let me know. Thank you.

Most important info, is the logo, website and the words "Cleaner" or "Clean" along "Protectant" or "Protect" the remainder is of less importance. Highlight: www.brightharborwash.example Focus is on company brand for Brighter Harbor Cleaner product: However, need a section for the following contact info: Walt Ferris (xxx) xxx-xxxx email address Would like space for QR Code if possible.

Target Market(s)

Adults in the USA between ages of 35-75 that are actively involved in the Recreational Vehicle (RV), travel trailer, and hot rod lifestyle. We are targeting the RV marked of the high end travel, 5th wheel and bus RV market. Along with hot rods, automotive and motorcycle market.

Industry/Entity Type

Travel

Requirements
Must have
• Most important info, is the logo, website and the words "Cleaner" or "Clean" along "Protectant" or "Protect" the remainder is of less importance.

Highlight:
www.brightharborwash.example

Focus is on company brand for Brighter Harbor Cleaner product: However, need a section for the following contact info:

Walt Ferris
(xxx) xxx-xxxx
email address
Nice to have
• Would like a space for a QR Code.

```html
<!DOCTYPE html>
<html lang="en">
<head>
<meta charset="utf-8">
<title>Bright Harbor, LLC — Business Card</title>
<link rel="stylesheet" href="https://fonts.googleapis.com/css2?family=Lora:wght@400;700&display=swap">
<style>
  :root {
    --backdrop: #e9e6e2;
    --card: #ffffff;
    --navy: #23407f;
    --gold: #f2b11c;
    --ink: #2f2f2f;
    --muted: #555555;
    --rule: #6b6b6b;
    --qr-frame: #b9b9b9;
  }
  * { box-sizing: border-box; margin: 0; padding: 0; }
  html, body {
    width: 1200px; height: 914px; overflow: hidden;
    background: var(--backdrop);
  }
  .canvas { position: relative; width: 1200px; height: 914px; }
  .card {
    position: absolute; left: 250px; width: 700px; height: 400px;
    background: var(--card);
    box-shadow: 0 6px 18px rgba(0,0,0,0.12);
    font-family: "Lora", serif;
  }
  .card--front { top: 37px; }
  .card--back { top: 477px; }

  /* Front */
  .front-brand {
    position: absolute; left: 0; right: 0; top: 190px;
    display: flex; flex-direction: column; align-items: center;
  }
  .front-brand__name {
    font-weight: 400; font-size: 44px; letter-spacing: 1px;
    color: var(--navy); line-height: 1.1;
  }
  .front-brand__tagline {
    margin-top: 10px;
    font-weight: 400; font-size: 20px; letter-spacing: 3px;
    text-transform: uppercase; color: var(--muted);
  }
  .front-brand__website {
    margin-top: 26px;
    font-weight: 700; font-size: 22px; color: var(--navy);
    border-top: 2px solid var(--gold); padding-top: 10px;
  }

  /* Back */
  .brand-block {
    position: absolute; left: 40px; top: 96px; width: 300px;
    display: flex; align-items: center; gap: 12px;
  }
  .brand-dot {
    width: 16px; height: 16px; border-radius: 50%;
    background: var(--gold); flex: none;
  }
  .brand-name {
    font-weight: 400; font-size: 30px; color: var(--navy); white-space: nowrap;
  }
  .brand-tagline {
    position: absolute; left: 68px; top: 142px;
    font-size: 13px; letter-spacing: 2px; text-transform: uppercase; color: var(--muted);
  }
  .qr-space {
    position: absolute; left: 68px; top: 190px; width: 110px; height: 110px;
    border: 1.5px dashed var(--qr-frame);
  }
  .divider {
    position: absolute; left: 365px; top: 60px; width: 1px; height: 280px;
    background: var(--rule);
  }
  .person { position: absolute; left: 400px; top: 84px; }
  .person__name {
    font-weight: 700; font-size: 28px; color: var(--navy); line-height: 1.1;
  }
  .person__role {
    font-weight: 400; font-size: 16px; color: var(--muted); margin-top: 4px;
  }
  .contacts {
    position: absolute; left: 400px; top: 180px; list-style: none;
    font-size: 15px; color: var(--ink);
  }
  .contacts li {
    display: flex; align-items: flex-start; gap: 12px;
    line-height: 1.3; margin-bottom: 9px;
  }
  .contacts .contacts__web { color: var(--navy); font-weight: 700; }
  .contacts svg { width: 18px; height: 18px; flex: none; fill: var(--navy); margin-top: 1px; }
</style>
</head>
<body>
<main class="canvas">

  <section class="card card--front" aria-label="Card front">
    <div class="front-brand">
      <p class="front-brand__name">Bright Harbor, LLC</p>
      <p class="front-brand__tagline">Cleaner and Protectant</p>
      <p class="front-brand__website">www.brightharborwash.example</p>
    </div>
  </section>

  <section class="card card--back" aria-label="Card back">
    <div class="brand-block">
      <span class="brand-dot"></span>
      <span class="brand-name">Bright Harbor</span>
    </div>
    <p class="brand-tagline">Cleaner &amp; Protectant</p>
    <div class="qr-space" role="img" aria-label="Space reserved for QR code"></div>

    <div class="divider"></div>

    <div class="person">
      <p class="person__name">Walt Ferris</p>
      <p class="person__role">Managing Director</p>
    </div>

    <ul class="contacts">
      <li>
        <svg viewBox="0 0 20 20" aria-hidden="true"><path d="M5 2l3 0 1.5 4-2 1.5c1 2.2 2.8 4 5 5l1.5-2 4 1.5v3c0 1-1 2-2 2C9 17 3 11 3 4c0-1 1-2 2-2z"/></svg>
        <span>(555) 014-2750</span>
      </li>
      <li>
        <svg viewBox="0 0 20 20" aria-hidden="true"><path d="M1 4h18v12H1z" fill="none" stroke="#23407f" stroke-width="2"/><path d="M1 4l9 7 9-7" fill="none" stroke="#23407f" stroke-width="2"/></svg>
        <span>walt@brightharborwash.example</span>
      </li>
      <li>
        <svg viewBox="0 0 20 20" aria-hidden="true"><circle cx="10" cy="10" r="8.5" fill="none" stroke="#23407f" stroke-width="1.8"/><ellipse cx="10" cy="10" rx="3.5" ry="8.5" fill="none" stroke="#23407f" stroke-width="1.5"/><path d="M1.5 10h17" stroke="#23407f" stroke-width="1.5"/></svg>
        <span class="contacts__web">www.brightharborwash.example</span>
      </li>
      <li>
        <svg viewBox="0 0 20 20" aria-hidden="true"><path d="M10 2L1 10h3v8h5v-5h2v5h5v-8h3z"/></svg>
        <span>Your Adress Inc 2nd Lane<br>Ave Millbrook, NJ 00000</span>
      </li>
    </ul>
  </section>

</main>
</body>
</html>
```